Business card design for my company.
I would like the card's background colour to be black. You can also see our web site to get an idea of our brand. https://www.tmwhomecrafting.com.au/
- Name
- Email

```html
<!DOCTYPE html>
<html lang="en">
<head>
<meta charset="utf-8">
<title>TMW Home Crafting – Business Card</title>
<link rel="stylesheet" href="https://fonts.googleapis.com/css2?family=Quicksand:wght@500;600;700&display=swap">
<style>
  :root {
    --page: #e9e7e3;
    --card: #060807;
    --green: #1f9443;
    --white: #f2f2f2;
    --rule: #1c7a3a;
  }
  * { box-sizing: border-box; margin: 0; padding: 0; }
  html, body { width: 1200px; height: 900px; overflow: hidden; }
  body {
    background: var(--page);
    font-family: "Quicksand", sans-serif;
    color: var(--white);
    position: relative;
  }
  .card {
    position: absolute;
    left: 250px;
    width: 700px;
    height: 400px;
    background: var(--card);
    border-radius: 36px;
    box-shadow: 0 10px 30px rgba(0,0,0,.25);
    overflow: hidden;
  }
  .card--back { top: 30px; }
  .card--front { top: 470px; }

  .web-address {
    position: absolute;
    top: 40px;
    right: 48px;
    font-size: 17px;
    font-weight: 600;
    letter-spacing: 3px;
  }
  .web-address .domain { color: var(--green); }

  .brand {
    position: absolute;
    display: flex;
    align-items: center;
    gap: 14px;
    font-weight: 700;
    font-size: 30px;
    letter-spacing: 3px;
    color: var(--white);
    text-transform: uppercase;
  }
  .brand__mark {
    width: 22px;
    height: 22px;
    background: var(--green);
    flex: none;
  }
  .card--back .brand { left: 60px; bottom: 70px; }
  .card--front .brand { right: 50px; top: 90px; }

  .contact { position: absolute; left: 50px; right: 50px; bottom: 40px; }
  .contact__name {
    color: var(--green);
    font-size: 26px;
    font-weight: 600;
    text-transform: uppercase;
    letter-spacing: 0.5px;
  }
  .contact__row {
    display: flex;
    align-items: center;
    gap: 8px;
    font-size: 19px;
    font-weight: 600;
  }
  .contact__row svg { width: 18px; height: 18px; flex: none; }
  .contact__rule {
    height: 2px;
    background: var(--rule);
    margin: 14px 0;
  }
  .sep { margin: 0 4px; }
</style>
</head>
<body>

  <section class="card card--back">
    <p class="web-address">www.<span class="domain">tmwhomecrafting</span>.com.au</p>
    <div class="brand"><span class="brand__mark"></span>TMW Home Crafting</div>
  </section>

  <section class="card card--front">
    <div class="brand"><span class="brand__mark"></span>TMW Home Crafting</div>

    <div class="contact">
      <p class="contact__name">Dean Harlow</p>
      <p class="contact__row">General Manager<span class="sep">|</span>
        <svg viewBox="0 0 24 24" aria-hidden="true"><path fill="#1f9443" d="M6.6 10.8a15 15 0 0 0 6.6 6.6l2.2-2.2a1 1 0 0 1 1-.25 11.4 11.4 0 0 0 3.6.57 1 1 0 0 1 1 1V20a1 1 0 0 1-1 1A17 17 0 0 1 3 4a1 1 0 0 1 1-1h3.5a1 1 0 0 1 1 1c0 1.25.2 2.45.57 3.6a1 1 0 0 1-.25 1z"/></svg>
        0400 123 456</p>
      <div class="contact__rule"></div>
      <p class="contact__row">
        <svg viewBox="0 0 24 24" aria-hidden="true"><path fill="#1f9443" d="M2 5h20v14H2z"/><path fill="none" stroke="#060807" stroke-width="1.6" d="M2 5l10 8 10-8M2 19l8-7M22 19l-8-7"/></svg>
        info@tmwhomecrafting.com.au<span class="sep">|</span>
        <svg viewBox="0 0 24 24" aria-hidden="true"><path fill="#1f9443" d="M12 2a7 7 0 0 0-7 7c0 5 7 13 7 13s7-8 7-13a7 7 0 0 0-7-7zm0 9.5A2.5 2.5 0 1 1 12 6.5a2.5 2.5 0 0 1 0 5z"/></svg>
        Riverton, Tasmania, Australia</p>
    </div>
  </section>

</body>
</html>
```